Quiet Porch Podcast Cover Graphic

We need a graphic designed for a new podcast called "Quiet Porch." The graphic will be used on multiple podcasting platforms as the lead graphic advertising the podcast. The podcast consists of interviews of individuals sharing their life experiences including challenges, successes, lessons learned, and unexpected turns. The purpose of the podcast is to help listeners and participants learn from the life experiences of everyday neighbors. This podcast has a heavy Christian foundation on the parable of the good samaritan. We believe that through hearing the experiences of everyday neighbors, listeners can be strengthened, nourished, and aided to handle their own life challenges and trials. We would like the final design to be simple and reflective of the purpose and the parable of the good samaritan. The final design needs to have the title of the podcast, "Quiet Porch." We believe the best designs will limit the number of colors to less than 5 and will look good in a monochromatic version as well as a color version. We think the color white should be the main color. The graphic should be square in dimensions. We have considered having two hands grasping each other as if to lift the hand from below, but open to other creative simple takes to convey the lessons from the good samaritan.

```html
<!DOCTYPE html>
<html lang="en">
<head>
<meta charset="utf-8">
<title>Quiet Porch — Podcast Cover</title>
<link rel="stylesheet" href="https://fonts.googleapis.com/css2?family=Oswald:wght@600&family=Mr+Dafoe&display=swap">
<style>
  :root {
    --stage: #3a3a3a;
    --paper: #f6f7f7;
    --teal: #0c5a5a;
    --teal-deep: #0a3036;
    --teal-light: #5fd3d6;
    --line: #3c3f44;
    --line-soft: #b9bcc0;
    --skin-light: #d3cfc3;
    --skin-dark: #8d877a;
  }
  html, body {
    margin: 0;
    width: 767px;
    height: 1200px;
    overflow: hidden;
    background: var(--stage);
  }
  .cover {
    position: absolute;
    left: 33px;
    top: 250px;
    width: 700px;
    height: 700px;
    background: linear-gradient(160deg, #ffffff 0%, var(--paper) 60%, #eceeee 100%);
    overflow: hidden;
  }
  .cover-art {
    position: absolute;
    inset: 0;
    width: 700px;
    height: 700px;
  }
  .title {
    position: absolute;
    left: 0;
    width: 700px;
    text-align: center;
    margin: 0;
  }
  .title-script {
    top: 400px;
    font-family: "Mr Dafoe", cursive;
    font-weight: 400;
    font-size: 150px;
    line-height: 1;
    left: 10px;
    background: linear-gradient(20deg, var(--teal) 20%, var(--teal-light) 90%);
    -webkit-background-clip: text;
    background-clip: text;
    color: transparent;
    z-index: 2;
  }
  .title-main {
    top: 508px;
    font-family: "Oswald", "Arial Narrow", sans-serif;
    font-weight: 600;
    font-size: 172px;
    line-height: 1;
    letter-spacing: 2px;
    background: linear-gradient(180deg, var(--teal) 0%, var(--teal-deep) 100%);
    -webkit-background-clip: text;
    background-clip: text;
    color: transparent;
    z-index: 1;
  }
</style>
</head>
<body>
  <section class="cover">
    <svg class="cover-art" viewBox="0 0 700 700" xmlns="http://www.w3.org/2000/svg">
      <defs>
        <linearGradient id="hands-tone" x1="0" y1="0" x2="1" y2="1">
          <stop offset="0" stop-color="var(--skin-light)"/>
          <stop offset="0.6" stop-color="#b3ad9f"/>
          <stop offset="1" stop-color="var(--skin-dark)"/>
        </linearGradient>
      </defs>
      <g class="frame-lines" fill="none" stroke-width="2.5">
        <path d="M170 29 H608 V120" stroke="var(--line)"/>
        <path d="M180 38 H628 V160" stroke="var(--line)"/>
        <path d="M200 56 H645 V200" stroke="var(--line)"/>
        <path d="M62 190 V640" stroke="var(--line-soft)"/>
        <path d="M74 250 V650" stroke="var(--line-soft)"/>
        <path d="M88 300 V620" stroke="var(--line-soft)"/>
      </g>
      <polygon class="brush-band" fill="var(--teal)"
        points="0,280 60,250 190,210 360,150 520,110 610,95 700,80 700,300 560,330 420,380 260,420 120,440 30,450 0,440"/>
      <polygon class="hands-photo" role="img" aria-label="Photo of one hand grasping another by the wrist to lift it up"
        fill="url(#hands-tone)"
        points="0,0 190,0 330,70 470,170 620,260 700,300 700,560 600,560 470,480 360,420 250,330 120,240 0,225"/>
    </svg>
    <p class="title title-script">Quiet</p>
    <h1 class="title title-main">PORCH</h1>
  </section>
</body>
</html>
```